Business card design for my company.
I would like the card's background colour to be black. You can also see our web site to get an idea of our brand. https://www.tmwhomecrafting.com.au/
- Name
- Email

```html
<!DOCTYPE html>
<html lang="en">
<head>
<meta charset="utf-8">
<title>TMW Home Crafting – Business Card</title>
<link href="https://fonts.googleapis.com/css2?family=Montserrat:wght@400;500;700&display=swap" rel="stylesheet">
<style>
  :root {
    --stage: #2b2b2b;
    --card: #141414;
    --green: #149447;
    --white: #f2f2f2;
    --silver: #bdbdbd;
  }
  html, body {
    margin: 0;
    padding: 0;
    width: 1200px;
    height: 689px;
    overflow: hidden;
    background: var(--stage);
    font-family: "Montserrat", sans-serif;
  }
  .stage {
    position: relative;
    width: 1200px;
    height: 689px;
    display: flex;
    align-items: center;
    justify-content: center;
    gap: 50px;
  }
  .card {
    position: relative;
    width: 525px;
    height: 300px;
    border-radius: 22px;
    background: var(--card);
    overflow: hidden;
    box-shadow: 0 18px 40px rgba(0,0,0,.45);
  }

  /* Pattern side */
  .card--pattern {
    border: 1px solid var(--green);
    box-sizing: border-box;
  }
  .pattern-fill {
    position: absolute;
    inset: 0;
    background: linear-gradient(120deg, #d9d9d9 0%, #8a8a8a 28%, #3a3a3a 50%, #111 75%, #0b0b0b 100%);
    opacity: .55;
  }
  .pattern-brand {
    position: absolute;
    left: 50%;
    top: 50%;
    transform: translate(-50%, -50%);
    display: flex;
    align-items: center;
    gap: 8px;
    padding: 8px 12px;
    background: var(--card);
    border-radius: 4px;
  }
  .pattern-brand .brand-square {
    width: 10px;
    height: 10px;
    background: var(--green);
  }
  .pattern-brand .brand-name {
    color: var(--white);
    font-weight: 700;
    font-size: 13px;
    letter-spacing: .12em;
  }

  /* Contact side */
  .card--contact {
    display: flex;
    align-items: center;
    padding: 0 34px;
    box-sizing: border-box;
  }
  .brand-block {
    display: flex;
    align-items: center;
    gap: 12px;
    width: 215px;
  }
  .brand-block .brand-square {
    width: 18px;
    height: 18px;
    background: var(--green);
    flex: none;
  }
  .brand-block .brand-name {
    color: var(--white);
    font-weight: 700;
    font-size: 22px;
    line-height: 1.15;
    letter-spacing: .06em;
  }
  .divider {
    width: 2px;
    height: 110px;
    background: var(--green);
    margin: 0 22px 0 14px;
  }
  .contact {
    color: var(--white);
  }
  .contact .person-name {
    margin: 0;
    color: var(--green);
    font-weight: 700;
    font-size: 26px;
  }
  .contact .person-role {
    margin: 4px 0 16px;
    font-weight: 400;
    font-size: 15px;
  }
  .contact .email {
    display: flex;
    align-items: center;
    gap: 8px;
    font-size: 12.5px;
  }
  .contact .email svg { flex: none; }
</style>
</head>
<body>
  <main class="stage">
    <section class="card card--pattern">
      <div class="pattern-fill" role="img" aria-label="Repeating brand pattern fading from silver to black"></div>
      <div class="pattern-brand">
        <span class="brand-square"></span>
        <span class="brand-name">TMW HOME CRAFTING</span>
      </div>
    </section>

    <section class="card card--contact">
      <div class="brand-block">
        <span class="brand-square"></span>
        <span class="brand-name">TMW HOME<br>CRAFTING</span>
      </div>
      <div class="divider"></div>
      <div class="contact">
        <h1 class="person-name">Liam Hartley</h1>
        <p class="person-role">General Manager</p>
        <p class="email">
          <svg width="14" height="10" viewBox="0 0 14 10" aria-hidden="true">
            <rect x="0" y="0" width="14" height="10" fill="var(--green)"/>
            <path d="M0 0 L7 5.5 L14 0" fill="none" stroke="var(--card)" stroke-width="1.2"/>
          </svg>
          info@tmwhomecrafting.com.au
        </p>
      </div>
    </section>
  </main>
</body>
</html>
```